TA BRAMLEY BUSINESS CARD DESIGN PROJECT

We need to utilize our logo that was expertly created on PixelHarbor and now need to match this with a business card design.

```html
<!DOCTYPE html>
<html lang="en">
<head>
<meta charset="utf-8">
<title>TA Bramley Business Card</title>
<link rel="stylesheet" href="https://fonts.googleapis.com/css2?family=Montserrat:wght@400;700&display=swap">
<style>
  :root {
    --stage: #2b2b2b;
    --card-black: #141414;
    --card-back: #161616;
    --emboss: #2a2a2a;
    --brand-blue: #1256ad;
    --stripe-black: #0d0d0d;
    --text-white: #f2f2f2;
  }
  * { box-sizing: border-box; margin: 0; padding: 0; }
  html, body {
    width: 1200px; height: 689px; overflow: hidden;
    background: var(--stage);
    font-family: "Montserrat", sans-serif;
  }
  .stage { position: relative; width: 1200px; height: 689px; }
  .card {
    position: absolute; top: 196px;
    width: 520px; height: 297px;
    border-radius: 18px; overflow: hidden;
  }
  .card-back { left: 50px; background: var(--card-back); }
  .card-front { left: 630px; background: var(--card-black); }

  .back-name {
    position: absolute; inset: 0;
    display: flex; align-items: center; justify-content: center;
    font-weight: 700; font-size: 54px; letter-spacing: 6px;
    color: var(--emboss);
  }

  .front-shapes { position: absolute; inset: 0; width: 520px; height: 297px; }

  .brand-name {
    position: absolute; left: 34px; top: 56px;
    font-weight: 700; font-size: 30px; letter-spacing: 4px;
    color: var(--text-white);
  }

  .person { position: absolute; left: 34px; top: 178px; }
  .person-name {
    font-weight: 700; font-size: 17px; letter-spacing: 1px; line-height: 20px;
    color: var(--brand-blue);
  }
  .person-role { font-size: 12px; color: var(--text-white); margin-top: 2px; }

  .divider {
    position: absolute; left: 200px; right: 24px; top: 190px;
    height: 1px; background: var(--brand-blue);
  }

  .contacts { position: absolute; left: 34px; top: 224px; list-style: none; }
  .contacts li {
    display: flex; align-items: center; gap: 8px;
    font-size: 11.5px; color: var(--text-white); line-height: 20px;
  }
  .contacts svg { width: 11px; height: 11px; fill: var(--brand-blue); }

  .address {
    position: absolute; right: 24px; top: 146px;
    text-align: right; font-size: 12px; line-height: 17px;
    color: var(--text-white);
  }
</style>
</head>
<body>
<main class="stage">
  <section class="card card-back" aria-label="Card back">
    <div class="back-name">TA BRAMLEY</div>
  </section>

  <section class="card card-front" aria-label="Card front">
    <svg class="front-shapes" viewBox="0 0 520 297" aria-hidden="true">
      <path d="M0,0 H480 C400,30 330,85 250,110 C170,132 90,136 0,140 Z" fill="var(--brand-blue)"/>
      <path d="M488,10 C405,45 335,96 252,120 C172,142 90,146 0,150" fill="none" stroke="var(--stripe-black)" stroke-width="7"/>
      <path d="M500,22 C415,58 345,106 258,130 C178,150 95,154 0,158" fill="none" stroke="var(--brand-blue)" stroke-width="3"/>
    </svg>

    <div class="brand-name">TA BRAMLEY</div>

    <div class="person">
      <p class="person-name">HOLLIS REED</p>
      <p class="person-role">Managing Director</p>
    </div>
    <div class="divider"></div>

    <ul class="contacts">
      <li><svg viewBox="0 0 12 12"><path d="M2 1h3l1 3-2 1a7 7 0 0 0 3 3l1-2 3 1v3a1 1 0 0 1-1 1A10 10 0 0 1 1 2a1 1 0 0 1 1-1z"/></svg>555 210 4487</li>
      <li><svg viewBox="0 0 12 12"><path d="M0 2h12v8H0z M0 2l6 5 6-5" /></svg>hello@tabramley.co</li>
      <li><svg viewBox="0 0 12 12"><circle cx="6" cy="6" r="6"/></svg>www.tabramley.co</li>
    </ul>

    <p class="address">418 Marlow Ridge Rd<br>Ashford, OH 44021</p>
  </section>
</main>
</body>
</html>
```